Website visual upgrade

I am seeking expressions of interest for the updating the visuals of my website www.kelvastaffing.net
I am basically seeking a simple,bold and visually strong graphic makeover.using existing or shortly to be modified text.

```html
<!DOCTYPE html>
<html lang="en">
<head>
<meta charset="utf-8">
<title>Kelva Staffing</title>
<link href="https://fonts.googleapis.com/css2?family=Roboto:wght@300;400;500&display=swap" rel="stylesheet">
<style>
:root{
  --red:#c8102e;
  --dark:#333333;
  --ink:#555555;
  --page:#ffffff;
  --card:#f1f1f1;
  --card-edge:#dddddd;
  --footer:#4a4a4a;
  --footer-text:#d6d6d6;
  --blue:#1a7fc1;
}
*{margin:0;padding:0;box-sizing:border-box}
html,body{width:960px;height:1200px;overflow:hidden}
body{position:relative;background:var(--page);font-family:'Roboto',sans-serif;color:var(--ink)}
.abs{position:absolute}
.header-band{left:0;top:0;width:960px;height:118px;background:linear-gradient(#f4f4f4,#ffffff)}
.brand{left:104px;top:44px;display:flex;align-items:center;gap:12px}
.brand-dot{width:30px;height:30px;border-radius:50%;background:var(--dark)}
.brand-name{font-size:30px;font-weight:500;color:var(--red);letter-spacing:.5px}
.contact{right:103px;top:36px;text-align:right}
.contact-phone{font-size:19px;color:var(--red);display:flex;align-items:center;justify-content:flex-end;gap:8px;letter-spacing:.5px}
.contact-mail{font-size:11px;color:var(--blue);display:flex;align-items:center;justify-content:flex-end;gap:8px;margin-top:4px}
.hero-photo{left:0;top:118px;width:960px;height:409px;background:linear-gradient(90deg,#e9ecef 0%,#dfe3e7 45%,#c9d6e4 65%,#e59a55 85%,#b8c7d8 100%)}
.nav{left:105px;top:102px;width:752px;height:36px;background:var(--dark);border-radius:3px;display:flex;justify-content:space-around;align-items:center;padding:0 6px}
.nav a{color:#fff;text-decoration:none;font-size:9.6px;letter-spacing:.3px}
.hero-title{left:104px;top:253px;height:42px;padding:0 13px;background:rgba(40,40,40,.92);color:#fff;font-size:22px;line-height:42px;letter-spacing:.3px}
.hero-sub{left:104px;top:298px;width:447px;height:62px;background:rgba(255,255,255,.88);color:var(--red);font-size:14.4px;font-weight:500;line-height:21px;padding:10px 13px}
.dots{left:104px;top:487px;display:flex;gap:4px}
.dots span{width:16px;height:16px;border-radius:50%;background:#f2f2f2}
.dots span.on{background:#d62020}
.section-title{font-size:19px;font-weight:400;color:var(--dark);letter-spacing:.3px}
.section-title em{font-style:normal;color:var(--red)}
.intro{left:0;top:545px;width:960px;text-align:center}
.intro p{width:720px;margin:10px auto 0;font-size:10.4px;line-height:20px;letter-spacing:.2px}
.card{top:661px;width:240px;height:265px;background:linear-gradient(#f1f1f1,#f9f9f9);border:1px solid var(--card-edge);border-radius:3px;box-shadow:0 1px 2px rgba(0,0,0,.15);text-align:center}
.card .section-title{font-size:16px;text-align:left;padding:14px 0 0 15px}
.card-photo{width:210px;height:93px;margin:8px auto 0;border-radius:3px}
.card p{font-size:10px;line-height:16px;padding:8px 12px 0;height:83px}
.btn{display:inline-block;margin-top:6px;background:#444;color:#fff;font-size:10.4px;padding:4px 9px;border-radius:3px}
.supports{left:104px;top:942px;width:752px;height:131px;background:var(--card);border:1px solid var(--card-edge);border-radius:3px;box-shadow:0 1px 2px rgba(0,0,0,.15)}
.supports .section-title{text-align:center;font-size:16px;padding-top:12px}
.support{top:38px;width:357px;height:82px;background:#fff;border:1px solid #d8d8d8;border-radius:3px;display:flex;align-items:center}
.support p{font-size:9.6px;line-height:16px;color:var(--ink)}
.badge{flex:none}
.footer{left:0;top:1088px;width:960px;height:112px;background:var(--footer);color:var(--footer-text)}
.footer-links{left:104px;top:20px;font-size:10.4px;letter-spacing:.3px}
.footer-links span{margin:0 13px}
.copy{left:104px;top:59px;font-size:9.6px;line-height:19px;color:#bdbdbd}
.copy b{color:#fff;font-weight:500}
.connect{left:740px;top:17px;font-size:12px;color:#fff}
.social{left:741px;top:47px;display:flex;gap:6px}
.social span{width:24px;height:24px;border-radius:3px;background:#6a6a6a}
</style>
</head>
<body>
<div class="abs header-band"></div>
<div class="abs brand"><span class="brand-dot"></span><span class="brand-name">Kelva Staffing</span></div>
<div class="abs contact">
  <div class="contact-phone">
    <svg width="15" height="11" viewBox="0 0 15 11"><path d="M1 4 Q7.5 -1 14 4 L12 5 L10 3 L5 3 L3 5 Z" fill="#777"/><rect x="3" y="6" width="9" height="5" rx="1" fill="#777"/></svg>
    61-3-95550142
  </div>
  <div class="contact-mail">
    <svg width="15" height="10" viewBox="0 0 15 10"><rect x=".5" y=".5" width="14" height="9" fill="none" stroke="#888"/><path d="M.5 .5 L7.5 6 L14.5 .5" fill="none" stroke="#888"/></svg>
    admin@kelvastaffing.net
  </div>
</div>
<div class="abs hero-photo" role="img" aria-label="Photo of a smiling construction worker in hard hat and orange safety vest leaning over a laptop"></div>
<nav class="abs nav">
  <a>HOME</a><a>WHO WE ARE</a><a>OUR APPROACH</a><a>WHAT WE DO</a><a>MIGRATION ASSISTANCE</a><a>JOB SEEKERS</a><a>USEFUL LINKS</a><a>SUPPORT</a><a>CONTACT US</a>
</nav>
<div class="abs hero-title">Lorem ipsum dolor sit amet</div>
<div class="abs hero-sub">Vestibulum vel metus sit amet turpis bibendum tincidunt vel sit amet quam.lobortis turpis in odio blandit ac interdum</div>
<div class="abs dots"><span class="on"></span><span></span><span></span><span></span></div>

<section class="abs intro">
  <h2 class="section-title"><em>WHO</em> WE ARE</h2>
  <p>We are committed to providing the highest standards &nbsp;of service in Executive search and selection and the provision of Skilled trades people and allied Health professionals throughout Australia. We have offices throughout Australia, clearly adding value to our clients’ strategic needs, wherever they may be.</p>
</section>

<article class="abs card" style="left:104px">
  <h3 class="section-title"><em>WHAT</em> WE DO</h3>
  <div class="card-photo" role="img" aria-label="Photo of a smiling group of healthcare professionals" style="background:linear-gradient(90deg,#d9c3b0,#eae3dc,#c7ad95,#6d8a4a)"></div>
  <p>We are a specialist recruiter to the Health sector. &nbsp;Our clienes andts are primarily engaged in the management of acute hospitals, residential aged &nbsp;care facilities community care service..</p>
  <span class="btn">Read More</span>
</article>
<article class="abs card" style="left:360px">
  <h3 class="section-title"><em>OUR</em> APPROACH</h3>
  <div class="card-photo" role="img" aria-label="Photo of business people shaking hands in a meeting" style="background:linear-gradient(90deg,#2f3d5c,#8c98a8,#3a3a46,#d8d4d0)"></div>
  <p>We think laterally about our clients’ needs and deliver &nbsp;a “fresh approach” to Executive search and selection &nbsp;and the provision of Skilled trades people and allied Health recruitment.</p>
  <span class="btn">Read More</span>
</article>
<article class="abs card" style="left:616px">
  <h3 class="section-title"><em>MIGRATION</em> ASSISTANCE</h3>
  <div class="card-photo" role="img" aria-label="Photo of a family standing in front of a recruitment office sign" style="background:linear-gradient(90deg,#3a2a22,#8a7a6a,#2a2220,#c9c3b8)"></div>
  <p>We can provide processing assistance to employers who are seeking suitably skilled and experienced staff from overseas on an appropriate temporary/permanent business visa.</p>
  <span class="btn">Read More</span>
</article>

<section class="abs supports">
  <h2 class="section-title"><em>OUR</em> SUPPORTS</h2>
  <div class="abs support" style="left:11px">
    <div class="badge" style="width:150px;display:flex;justify-content:center"><span style="font-size:18px;font-weight:500;color:var(--red)">BrightPath</span></div>
    <p style="padding-right:20px">BrightPath’s mission is to support, develop and empower &nbsp;young people living with cancer.</p>
  </div>
  <div class="abs support" style="left:383px">
    <div class="badge" style="width:100px;display:flex;justify-content:center"><span style="width:60px;height:64px;background:#111;display:block"></span></div>
    <p style="padding-right:12px">The Kinara Community Fund supports a range of community &nbsp;projects focused on young people in Africa and Australia.</p>
  </div>
</section>

<footer class="abs footer">
  <div class="abs footer-links">Home<span>/</span>Contact Us<span>/</span>Privacy Policy<span>/</span>Site Map</div>
  <div class="abs copy">Copyright 2013. <b>Kelva Partners.</b><br>All Right Reserved</div>
  <div class="abs connect">Connect Us</div>
  <div class="abs social" aria-label="Social links"><span></span><span></span><span></span><span></span></div>
</footer>
</body>
</html>
```